Design and Renovation Company Luxury Business Card

I want to create a luxury business card for a Design and Renovation Firm . We will use our current logo. The company name is 528BUILDA. We do not want anything standard. We need a very unique concept.
Please see uploaded inspiration. I really like the textured paper option. I would like the card to be thick with debossing, and/or embossing options. The logo has orange in it but I would like to see the card with and without the orange. I think the orange may make the company feel less high-end. The goal is to elevate the logo not match its vibe per se of the logo. We want something very unique, not standard at all!
I would like a space for :
Logo,
Name,
Position,
Email,
Office number,
Website Address,
Business Address,
Thank you!
Have fun!
Target Market(s)
Home owners Age 35 +
Industry/Entity Type
Design and Renovation
Contact Information for Business Card
Logo, Name, Position, Email, Office number, Website Address, Business Address,.
Colors
Designer to choose colors to be used in the design.
Requirements
Must have
- A luxury designer feel. Must be black or dark grey but open to other luxury ideas.
Nice to have
- Gold, silver, black embossing or debossing. Textured paper design.
Should not have
- A cheap look and feel.

```html
<!DOCTYPE html>
<html lang="en">
<head>
<meta charset="utf-8">
<title>528BUILDA Business Card</title>
<link href="https://fonts.googleapis.com/css2?family=Montserrat:wght@400;600;700&display=swap" rel="stylesheet">
<style>
  :root {
    --stage: #1c1c1e;
    --card: #1a1a1a;
    --ink: #ffffff;
    --ink-soft: #d4d4d4;
    --rule: #bdbdbd;
    --tile-light: #5a5a5a;
    --tile-dark: #050505;
  }
  * { margin: 0; padding: 0; box-sizing: border-box; }
  html, body {
    width: 1200px; height: 801px; overflow: hidden;
    background: var(--stage);
    font-family: "Montserrat", sans-serif;
    color: var(--ink);
  }
  .stage {
    width: 1200px; height: 801px;
    display: flex; align-items: center; justify-content: center; gap: 40px;
  }
  .card {
    position: relative;
    width: 540px; height: 309px;
    border-radius: 18px;
    background: var(--card);
    overflow: hidden;
    box-shadow: 0 14px 34px rgba(0,0,0,.55);
  }
  /* Company name, set plainly in the card's text face */
  .company-name {
    position: absolute;
    font-weight: 600;
    letter-spacing: 0;
    line-height: 1;
    color: var(--ink);
  }

  /* Front */
  .card-front .company-name { left: 44px; top: 142px; font-size: 26px; }
  .divider { position: absolute; left: 262px; top: 82px; width: 1px; height: 150px; background: var(--rule); }
  .contact { position: absolute; left: 284px; top: 84px; }
  .contact-name { font-weight: 700; font-size: 19px; line-height: 1.1; }
  .contact-title { font-size: 11px; color: var(--ink-soft); margin-top: 3px; }
  .contact-address { font-size: 11px; color: var(--ink-soft); line-height: 1.4; margin-top: 14px; }
  .contact-list { list-style: none; margin-top: 12px; }
  .contact-list li { display: flex; align-items: center; gap: 8px; font-size: 11px; color: var(--ink-soft); line-height: 1.75; }
  .contact-list svg { width: 11px; height: 11px; flex: none; }

  /* Back */
  .tile-field {
    position: absolute; inset: 0;
    background: linear-gradient(200deg, var(--tile-light) 0%, #262626 40%, var(--tile-dark) 75%, #000 100%);
  }
  .card-back .company-name { left: 190px; top: 186px; font-size: 34px; }
</style>
</head>
<body>
<main class="stage">
  <section class="card card-front" aria-label="Business card front">
    <p class="company-name">528BUILDA</p>
    <span class="divider"></span>
    <div class="contact">
      <p class="contact-name">Daniel Reyes</p>
      <p class="contact-title">Managing Director</p>
      <p class="contact-address">418 Harlow Park Ave, #112<br>Brookmont, OH 43119</p>
      <ul class="contact-list">
        <li>
          <svg viewBox="0 0 12 12" aria-hidden="true"><circle cx="6" cy="6" r="6" fill="#fff"/><path d="M4 3.2l1.2 1.4-.6.8c.4.8 1 1.4 1.8 1.8l.8-.6 1.4 1.2-.8 1c-2 0-4.6-2.6-4.6-4.6z" fill="#1a1a1a"/></svg>
          614-555-0139
        </li>
        <li>
          <svg viewBox="0 0 12 12" aria-hidden="true"><rect x="1" y="2.5" width="10" height="7" fill="#fff"/><path d="M1 2.5l5 4 5-4" stroke="#1a1a1a" stroke-width="1" fill="none"/></svg>
          hello@528builda.com
        </li>
        <li>
          <svg viewBox="0 0 12 12" aria-hidden="true"><circle cx="6" cy="6" r="5.5" fill="#fff"/><path d="M.5 6h11M6 .5c-2.4 3-2.4 8 0 11M6 .5c2.4 3 2.4 8 0 11" stroke="#1a1a1a" stroke-width=".8" fill="none"/></svg>
          www.528builda.com
        </li>
      </ul>
    </div>
  </section>

  <section class="card card-back" aria-label="Business card back">
    <div class="tile-field" role="img" aria-label="Decorative field of glossy black and grey square tiles"></div>
    <p class="company-name">528BUILDA</p>
  </section>
</main>
</body>
</html>
```